Multi-Line Insurance PPC Landing Page - Conversion optimized.

We have a PPC landing page used for the general population to get an insurance quote through an agent's site.

We'd like to improve the page for PPC traffic, make it more conversion friendly.

Site should be a single long page.

We will dynamically change the form and headlines on the page depending on what insurance "line" is being called. ie, Lift, Auto, Home, Business.

The enclosed AI file has all of the raw elements we need. We're looking to enhance the design and conversion ability.

Target Market(s)

General public needed insurance services.

Industry/Entity Type

Insurance Broker

Number of Pages Required

1 page

Font styles to use
Sans Serif

Requirements
Must have
• Form, agent picture, name, address.

```html
<!DOCTYPE html>
<html lang="en">
<head>
<meta charset="utf-8">
<title>Insurance Agent – Get an Instant Quote</title>
<link href="https://fonts.googleapis.com/css2?family=Cinzel:wght@400;700&family=Lato:wght@400;700&display=swap" rel="stylesheet">
<style>
  :root {
    --blue: #1a8fd3;
    --blue-dark: #0d5ea8;
    --navy: #0b4d94;
    --ink: #333;
    --muted: #666;
    --grey-bg: #f0f0f0;
    --line: #d8d8d8;
    --white: #fff;
  }
  * { box-sizing: border-box; margin: 0; padding: 0; }
  html, body { width: 742px; height: 1200px; overflow: hidden; }
  body { font-family: "Lato", Arial, sans-serif; color: var(--ink); background: var(--white); position: relative; }

  .site-header { height: 45px; display: flex; align-items: center; justify-content: space-between; padding: 0 34px; }
  .brand { font-family: "Cinzel", Georgia, serif; font-weight: 700; font-size: 22px; color: var(--navy); letter-spacing: .5px; }
  .header-phone { display: flex; align-items: center; gap: 6px; color: var(--navy); font-weight: 700; font-size: 15px; }

  .hero { height: 250px; background: linear-gradient(180deg, #1f9ae0 0%, #1585c9 100%); position: relative; }
  .hero-text { position: absolute; left: 14px; top: 102px; color: var(--white); font-weight: 700; font-size: 17px; line-height: 1.3; width: 300px; }
  .btn-light { position: absolute; left: 14px; top: 172px; background: var(--white); color: var(--navy); font-size: 10px; font-weight: 700; padding: 6px 10px; }
  .hero-art { position: absolute; left: 300px; top: 30px; width: 280px; height: 200px; background: radial-gradient(ellipse at center, rgba(255,255,255,.35), rgba(255,255,255,.08) 70%); border-radius: 8px; }

  .quote-card { position: absolute; left: 50px; top: 297px; width: 612px; height: 268px; background: var(--white); border-top: 4px solid var(--blue); box-shadow: 0 2px 10px rgba(0,0,0,.18); display: flex; }
  .agent { width: 185px; text-align: center; padding-top: 18px; }
  .agent-photo { width: 68px; height: 78px; margin: 0 auto 6px; background: linear-gradient(180deg, #c8ccd2, #4a5563); }
  .agent-name { font-family: "Cinzel", Georgia, serif; color: var(--navy); font-size: 12px; font-weight: 700; }
  .agent-line { font-size: 9px; color: var(--muted); margin-top: 4px; display: flex; align-items: center; justify-content: center; gap: 4px; }
  .agent-addr { font-size: 9px; color: var(--muted); margin-top: 6px; line-height: 1.4; padding: 0 18px; }

  .quote-form { flex: 1; padding: 16px 24px 0 20px; }
  .quote-title { font-family: "Cinzel", Georgia, serif; color: var(--blue); font-size: 16px; font-weight: 700; text-align: center; margin-bottom: 10px; }
  .form-grid { display: grid; grid-template-columns: 1fr 1fr; column-gap: 22px; row-gap: 8px; }
  .field label { display: block; font-size: 8px; color: var(--muted); margin-bottom: 3px; }
  .input { height: 17px; border: 1px solid var(--line); background: var(--white); font-size: 8px; color: #999; padding: 3px 5px; position: relative; }
  .select::after { content: ""; position: absolute; right: 5px; top: 6px; border: 3px solid transparent; border-top-color: #999; }
  .dob { display: flex; gap: 5px; }
  .dob .input { flex: 1; }
  .submit { display: block; margin: 12px 90px 0 auto; background: var(--navy); color: var(--white); font-size: 9px; font-weight: 700; padding: 6px 22px; border: 0; }

  .section-title { font-family: "Cinzel", Georgia, serif; font-weight: 700; color: var(--navy); font-size: 18px; text-align: center; }
  .section-title .accent { color: var(--blue); }
  .title-rule { width: 150px; height: 1px; background: var(--blue); margin: 5px auto 0; position: relative; }
  .title-rule::after { content: ""; position: absolute; left: 71px; top: -3px; width: 7px; height: 7px; background: var(--blue); border-radius: 50%; }

  .about { position: absolute; top: 590px; left: 0; width: 742px; height: 110px; background: var(--grey-bg); padding-top: 18px; }
  .about p { font-size: 8.5px; color: var(--muted); text-align: center; line-height: 1.5; padding: 10px 40px 0; }

  .products { position: absolute; top: 722px; left: 0; width: 742px; }
  .product-row { display: flex; justify-content: center; gap: 48px; margin-top: 16px; }
  .product { width: 116px; text-align: center; }
  .product-icon { width: 50px; height: 50px; margin: 0 auto; background: var(--navy); border-radius: 6px; }
  .product h3 { font-family: "Cinzel", Georgia, serif; font-weight: 700; color: var(--blue); font-size: 12px; margin-top: 6px; }
  .product p { font-size: 8px; color: var(--muted); line-height: 1.4; margin-top: 3px; }
  .btn-dark { display: inline-block; margin-top: 7px; background: var(--navy); color: var(--white); font-size: 8px; font-weight: 700; padding: 5px 12px; }

  .testimonials { position: absolute; top: 952px; left: 0; width: 742px; }
  .testi-row { display: flex; justify-content: center; align-items: flex-start; gap: 70px; margin-top: 10px; position: relative; }
  .avatar { border-radius: 50%; background: linear-gradient(180deg, #d9d9d9, #9a9a9a); }
  .avatar.side { width: 62px; height: 62px; margin-top: 14px; }
  .avatar.main { width: 62px; height: 62px; margin: 0 auto; border: 3px solid var(--white); box-shadow: 0 0 0 2px var(--blue); background: linear-gradient(180deg, #e0b8a8, #8a4d3c); }
  .testi-main { text-align: center; width: 220px; }
  .testi-name { font-family: "Cinzel", Georgia, serif; color: var(--blue); font-size: 11px; font-weight: 700; margin-top: 5px; }
  .testi-main p { font-size: 8px; color: var(--muted); line-height: 1.35; margin-top: 2px; }
  .arrow { position: absolute; top: 32px; }
  .arrow.left { left: 22px; }
  .arrow.right { right: 22px; }

  .site-footer { position: absolute; top: 1120px; left: 0; width: 742px; height: 80px; background: var(--navy); color: var(--white); text-align: center; padding-top: 9px; }
  .site-footer h4 { font-size: 9px; font-weight: 700; }
  .site-footer p { font-size: 8px; line-height: 1.4; padding: 2px 50px 0; opacity: .9; }
  .site-footer .copy { margin-top: 8px; }
</style>
</head>
<body>

<header class="site-header">
  <div class="brand">Insurance Agent</div>
  <div class="header-phone">
    <svg width="16" height="16" viewBox="0 0 24 24" aria-hidden="true"><circle cx="12" cy="12" r="11" fill="none" stroke="#0b4d94" stroke-width="2"/><path d="M9 6.5l1.6 2.8-1.3 1.2a7 7 0 004.2 4.2l1.2-1.3 2.8 1.6-.8 2a2 2 0 01-2 .9A10 10 0 016 8.5a2 2 0 01.9-2z" fill="#0b4d94"/></svg>
    123 456 7890
  </div>
</header>

<section class="hero">
  <div class="hero-text">Lorem ipsum dolor sit amet, consectetur adipiscing elit sed diam</div>
  <div class="btn-light">GET A QUOTE!</div>
  <div class="hero-art" role="img" aria-label="Illustration of a family standing under a protective umbrella"></div>
</section>

<section class="quote-card">
  <div class="agent">
    <div class="agent-photo" role="img" aria-label="Portrait photo of the insurance agent"></div>
    <div class="agent-name">Lorem Ipsum Dolor</div>
    <div class="agent-line">
      <svg width="9" height="9" viewBox="0 0 24 24" aria-hidden="true"><path d="M6 2l4 6-2.5 2.5a12 12 0 006 6L16 14l6 4-2 4A18 18 0 012 4z" fill="#0b4d94"/></svg>
      123 456 7890
    </div>
    <div class="agent-line">
      <svg width="10" height="8" viewBox="0 0 24 18" aria-hidden="true"><rect x="1" y="1" width="22" height="16" fill="none" stroke="#0b4d94" stroke-width="2"/><path d="M1 1l11 9 11-9" fill="none" stroke="#0b4d94" stroke-width="2"/></svg>
      info@agentsite.com
    </div>
    <div class="agent-addr">Lorem ipsum dolor sit, Lorem ipsum dolor sit amet 12345</div>
  </div>

  <div class="quote-form">
    <h2 class="quote-title">Get An Instant Insurance Quote</h2>
    <div class="form-grid">
      <div class="field"><label>First Name</label><div class="input"></div></div>
      <div class="field"><label>Street Address</label><div class="input"></div></div>
      <div class="field"><label>Zip</label><div class="input"></div></div>
      <div class="field"><label>Coverage Type</label><div class="input select">Select</div></div>
      <div class="field"><label>Date of Birth</label>
        <div class="dob"><div class="input select">Month</div><div class="input select">Day</div><div class="input select">Year</div></div>
      </div>
      <div class="field"><label>Phone</label><div class="input"></div></div>
      <div class="field"><label>Current Provider</label><div class="input select">Select</div></div>
      <div class="field"><label>Email</label><div class="input"></div></div>
    </div>
    <button class="submit">SUBMIT</button>
  </div>
</section>

<section class="about">
  <h2 class="section-title"><span class="accent">About</span> Insurance Agent</h2>
  <div class="title-rule"></div>
  <p>Lorem ipsum dolor sit amet, consectetur adipiscing elit, sed diam nonummy nibh euismod tincidunt ut laoreet dolore magna aliquam erat volutpat. Ut wisi enim ad minim veniam, quis nostrud exerci tation ullamcorper suscipit lobortis nisl ut aliquip ex ea commodo consequat. Duis autem vel eum iriure dolor in hendrerit in vulputate velit esse molestie consequat, vel illum dolore eu feugiat nulla facilisis.</p>
</section>

<section class="products">
  <h2 class="section-title"><span class="accent">Our</span> Insurance Products</h2>
  <div class="title-rule"></div>
  <div class="product-row">
    <div class="product">
      <div class="product-icon" role="img" aria-label="Forklift icon for lift insurance"></div>
      <h3>Lift</h3>
      <p>Lorem ipsum dolor sit amet, consectetur adipiscing elit, sed diam nonummy nibh euismod.</p>
      <div class="btn-dark">GET A QUOTE!</div>
    </div>
    <div class="product">
      <div class="product-icon" role="img" aria-label="Car icon for auto insurance"></div>
      <h3>Auto</h3>
      <p>Lorem ipsum dolor sit amet, consectetur adipiscing elit, sed diam nonummy nibh euismod.</p>
      <div class="btn-dark">GET A QUOTE!</div>
    </div>
    <div class="product">
      <div class="product-icon" role="img" aria-label="House icon for home insurance"></div>
      <h3>Home</h3>
      <p>Lorem ipsum dolor sit amet, consectetur adipiscing elit, sed diam nonummy nibh euismod.</p>
      <div class="btn-dark">GET A QUOTE!</div>
    </div>
    <div class="product">
      <div class="product-icon" role="img" aria-label="Briefcase icon for business insurance"></div>
      <h3>Business</h3>
      <p>Lorem ipsum dolor sit amet, consectetur adipiscing elit, sed diam nonummy nibh euismod.</p>
      <div class="btn-dark">GET A QUOTE!</div>
    </div>
  </div>
</section>

<section class="testimonials">
  <h2 class="section-title"><span class="accent">Client</span> Testimonials</h2>
  <div class="title-rule"></div>
  <div class="testi-row">
    <svg class="arrow left" width="14" height="26" viewBox="0 0 14 26" aria-hidden="true"><path d="M12 2L2 13l10 11" fill="none" stroke="#bbb" stroke-width="2"/></svg>
    <div class="avatar side" role="img" aria-label="Client photo"></div>
    <div class="testi-main">
      <div class="avatar main" role="img" aria-label="Featured client photo"></div>
      <div class="testi-name">Lorem Ipsum Dolor Sit</div>
      <p>Lorem ipsum dolor sit amet, consectetur adipiscing elit, sed diam nonummy nibh euismod tincidunt ut laoreet dolore magna.</p>
    </div>
    <div class="avatar side" role="img" aria-label="Client photo"></div>
    <svg class="arrow right" width="14" height="26" viewBox="0 0 14 26" aria-hidden="true"><path d="M2 2l10 11L2 24" fill="none" stroke="#bbb" stroke-width="2"/></svg>
  </div>
</section>

<footer class="site-footer">
  <h4>Disclaimer:</h4>
  <p>Lorem ipsum dolor sit amet, consectetur adipiscing elit, sed diam nonummy nibh euismod tincidunt ut laoreet dolore magna aliquam erat volutpat. Ut wisi enim ad minim veniam, quis nostrud exerci tation ullamcorper.</p>
  <p class="copy">Copyright 2016 Insurance Agent | All rights reserved</p>
</footer>

</body>
</html>
```